Maple Roster Business Card for recruitment company

We are looking for a Business Card Design that incorporates our personal details and our busines name and logo. We are a specialized search consultancy that recruit Property and Construction professionals.
We would like a business card that stands out and is appealing to the Construction and Property industry as well.

Target Market(s)

people in the construction and property industry

Contact Information for Business Card

Business Name and logo

Font styles to use
Serif

Colors
0094D4
00A9DD
6FCCEA
C7EBF8
E9F6FB

Requirements
Must have
• Business name and logo as well as contact details
Should not have
• No photos of us please

```html
<!DOCTYPE html>
<html lang="en">
<head>
<meta charset="utf-8">
<title>Maple Roster – Business Card</title>
<link rel="stylesheet" href="https://fonts.googleapis.com/css2?family=Josefin+Sans:wght@300;600&family=Arimo:wght@400&display=swap">
<style>
  :root {
    --teal: #053c50;
    --paper: #ffffff;
    --backdrop: #e4e4e4;
  }
  * { margin: 0; padding: 0; box-sizing: border-box; }
  html, body { width: 1200px; height: 900px; overflow: hidden; }
  body { background: var(--backdrop); position: relative; font-family: "Arimo", Arial, sans-serif; }

  .card { position: absolute; top: 217px; width: 309px; height: 500px; overflow: hidden; }
  .card-back {
    left: 279px; background: var(--teal);
    border-radius: 0 64px 0 64px;
  }
  .card-front {
    left: 617px; background: var(--paper);
    border-radius: 64px 0 64px 0;
  }

  .wordmark {
    position: absolute;
    left: 31px;
    width: 247px;
    font-family: "Josefin Sans", Arial, sans-serif;
    font-weight: 300;
    font-size: 32px;
    letter-spacing: 0;
    text-transform: uppercase;
    white-space: nowrap;
    line-height: 1;
  }
  .card-back .wordmark { top: 406px; color: var(--paper); }
  .card-front .wordmark { top: 134px; color: var(--teal); }

  .person { position: absolute; left: 32px; top: 308px; color: var(--teal); }
  .person-name {
    font-family: "Josefin Sans", Arial, sans-serif;
    font-weight: 600; font-size: 22px; line-height: 1; letter-spacing: 0.2px;
  }
  .person-role { font-size: 14px; margin-top: 2px; }

  .contacts { position: absolute; left: 32px; top: 360px; list-style: none; color: var(--teal); font-size: 14px; }
  .contacts li { display: flex; align-items: center; height: 18px; }
  .contacts svg { width: 12px; height: 12px; margin-right: 5px; fill: var(--teal); flex: none; }

  .address { position: absolute; left: 32px; top: 427px; color: var(--teal); font-size: 14px; line-height: 18px; font-style: normal; }
</style>
</head>
<body>
  <section class="card card-back">
    <div class="wordmark">Maple Roster</div>
  </section>

  <section class="card card-front">
    <div class="wordmark">Maple Roster</div>

    <div class="person">
      <div class="person-name">DANIEL HART</div>
      <div class="person-role">Managing Director</div>
    </div>

    <ul class="contacts">
      <li>
        <svg viewBox="0 0 24 24" aria-hidden="true"><path d="M6.6 10.8a15.1 15.1 0 0 0 6.6 6.6l2.2-2.2a1 1 0 0 1 1-.25 11.4 11.4 0 0 0 3.6.57 1 1 0 0 1 1 1V20a1 1 0 0 1-1 1A17 17 0 0 1 3 4a1 1 0 0 1 1-1h3.5a1 1 0 0 1 1 1c0 1.250.2 2.45.57 3.57a1 1 0 0 1-.25 1z"/></svg>
        044-987 654 321
      </li>
      <li>
        <svg viewBox="0 0 24 24" aria-hidden="true"><path d="M2 5h20v14H2z M3 6l9 7 9-7" fill="var(--teal)" stroke="#fff" stroke-width="1.5"/></svg>
        info@mapleroster.com
      </li>
      <li>
        <svg viewBox="0 0 24 24" aria-hidden="true"><g fill="none" stroke="var(--teal)" stroke-width="2"><circle cx="12" cy="12" r="10"/><ellipse cx="12" cy="12" rx="4" ry="10"/><path d="M2 12h20M4 7h16M4 17h16"/></g></svg>
        www.mapleroster.com
      </li>
    </ul>

    <address class="address">
      421, Address line goes here<br>
      45452,Country Name
    </address>
  </section>
</body>
</html>
```